Business Card Design (NEW FILES)

ATTENTION: New vector files are available. Please update your design to reflect/use the new (better resolution) logo images.

Seeking a unique and professional business card design for a commercial drone photography/videography business. The layout should feature
the logo (attached) and include the following information:
Owen Tarrick
614-502-7738
www.skylarkreelworks.example
NRD Certified Remote Pilot

Owen Tarrick

```html
<!DOCTYPE html>
<html lang="en">
<head>
<meta charset="utf-8">
<title>Skylark Reelworks — Business Card</title>
<link rel="stylesheet" href="https://fonts.googleapis.com/css2?family=Open+Sans:wght@400;600;700;800&display=swap">
<style>
  :root {
    --navy: #161a4b;
    --navy-deep: #11153d;
    --orange: #ee8a43;
    --white: #ffffff;
    --stage: #e6e7ec;
  }
  * { box-sizing: border-box; margin: 0; padding: 0; }
  html, body {
    width: 1200px; height: 780px; overflow: hidden;
    background: var(--stage);
    font-family: "Open Sans", Arial, sans-serif;
  }
  .sheet {
    width: 1200px; height: 780px;
    display: flex; align-items: center; justify-content: center; gap: 44px;
  }
  .card {
    position: relative;
    width: 540px; height: 309px;
    background: linear-gradient(160deg, var(--navy) 0%, var(--navy-deep) 100%);
    border-radius: 18px;
    border-bottom: 4px solid var(--orange);
    border-left: 3px solid var(--orange);
    box-shadow: 0 14px 30px rgba(10, 12, 40, .28);
    overflow: hidden;
    color: var(--white);
  }

  /* brand name lockup */
  .brand {
    display: flex; align-items: center; gap: 12px;
    font-weight: 700; color: var(--white);
    letter-spacing: .06em; text-transform: uppercase; line-height: 1;
  }
  .brand-dot {
    flex: none; border-radius: 50%; background: var(--orange);
  }

  /* front */
  .card-front { display: flex; align-items: center; justify-content: center; }
  .card-front .brand { font-size: 34px; }
  .card-front .brand-dot { width: 26px; height: 26px; }

  /* back */
  .card-back .brand {
    position: absolute; left: 36px; top: 58px; font-size: 21px; gap: 9px;
  }
  .card-back .brand-dot { width: 16px; height: 16px; }

  .name-tag {
    position: absolute; right: 0; top: 40px;
    display: flex; align-items: stretch;
  }
  .name-block { text-align: right; padding-right: 14px; }
  .person-name { font-size: 24px; font-weight: 800; line-height: 1.1; }
  .person-name .first { color: var(--orange); }
  .person-role { font-size: 13px; font-weight: 600; margin-top: 2px; }
  .name-bar { width: 16px; background: var(--orange); }

  .credentials {
    position: absolute; left: 36px; top: 142px;
    color: var(--orange); font-size: 15px; font-weight: 600; line-height: 1.45;
  }
  .contact {
    position: absolute; left: 36px; bottom: 26px;
    list-style: none; font-size: 13px; line-height: 1; 
  }
  .contact li { display: flex; align-items: center; gap: 10px; margin-top: 8px; }
  .contact svg { width: 15px; height: 15px; flex: none; }
</style>
</head>
<body>
<main class="sheet">

  <section class="card card-front" aria-label="Card front">
    <div class="brand"><span class="brand-dot"></span>Skylark Reelworks</div>
  </section>

  <section class="card card-back" aria-label="Card back">
    <div class="brand"><span class="brand-dot"></span>Skylark Reelworks</div>

    <div class="name-tag">
      <div class="name-block">
        <p class="person-name"><span class="first">Owen</span> Tarrick</p>
        <p class="person-role">Owner</p>
      </div>
      <div class="name-bar"></div>
    </div>

    <p class="credentials">NRD Certified Remote Pilot<br>Fully Insured</p>

    <ul class="contact">
      <li>
        <svg viewBox="0 0 24 24" aria-hidden="true"><path fill="#ee8a43" d="M6.6 10.8a15.1 15.1 0 0 0 6.6 6.6l2.2-2.2c.3-.3.7-.4 1-.2 1.1.4 2.3.6 3.6.6.6 0 1 .4 1 1V20c0 .6-.4 1-1 1A17 17 0 0 1 3 4c0-.6.4-1 1-1h3.5c.6 0 1 .4 1 1 0 1.2.2 2.4.6 3.6.1.3 0 .7-.2 1z"/></svg>
        614-502-7738
      </li>
      <li>
        <svg viewBox="0 0 24 24" aria-hidden="true"><circle cx="12" cy="12" r="9" fill="none" stroke="#ee8a43" stroke-width="2"/><path d="M3 12h18M12 3c3 3 3 15 0 18M12 3c-3 3-3 15 0 18" fill="none" stroke="#ee8a43" stroke-width="1.6"/></svg>
        www.skylarkreelworks.example
      </li>
      <li>
        <svg viewBox="0 0 24 24" aria-hidden="true"><rect x="3" y="6" width="18" height="13" rx="1.5" fill="none" stroke="#ee8a43" stroke-width="2"/><path d="M3.5 7l8.5 6.5L20.5 7" fill="none" stroke="#ee8a43" stroke-width="2"/></svg>
        info@skylarkreelworks.example
      </li>
    </ul>
  </section>

</main>
</body>
</html>
```